Colin Vardek Business card

Hey there, I’m hoping to have a business card designed. I’m in Real estate and just switched to a new Brokerage called: The Harbourline Property Group

The back could just be the company name maybe or whatever looks good!

I’ve attached some logos of our company and some cards my buddy had done up.

On the card:
Colin Vardek
colinvardek@mailora.com
587-412-9065
colinvardek.ca

Target Market(s)

Home buyers and sellers

Industry/Entity Type

Real Estate

Contact Information for Business Card

just looking for a cool and modern design with my picture on it. I like the idea of Black and red being used.

Requirements
Must have
• all the details provided. I'm open to anything. Just want a professional looking card.

```html
<!DOCTYPE html>
<html lang="en">
<head>
<meta charset="utf-8">
<title>Colin Vardek Business Card</title>
<link href="https://fonts.googleapis.com/css2?family=Poppins:wght@400;500;700;800&display=swap" rel="stylesheet">
<style>
  :root {
    --backdrop: #2a2a2c;
    --card-dark: #1c1c1f;
    --portrait-grey: #4b4b4d;
    --portrait-figure: #2b2b2f;
    --brand-red: #d2163a;
    --ink-white: #f5f5f5;
  }
  * { margin: 0; padding: 0; box-sizing: border-box; }
  html, body {
    width: 1200px;
    height: 1108px;
    overflow: hidden;
    background: var(--backdrop);
    font-family: "Poppins", sans-serif;
  }
  .card {
    position: absolute;
    top: 211px;
    width: 400px;
    height: 686px;
    border-radius: 26px;
    overflow: hidden;
    background: var(--card-dark);
    box-shadow: 0 18px 40px rgba(0,0,0,0.45);
  }
  .card-front { left: 160px; }
  .card-back { left: 640px; }

  .front-shapes { position: absolute; inset: 0; }

  .agent-name {
    position: absolute;
    left: 10px; width: 300px;
    top: 452px;
    text-align: center;
    color: var(--brand-red);
    font-weight: 500;
    font-size: 29px;
    line-height: 36px;
    letter-spacing: 0.5px;
    text-transform: uppercase;
    white-space: nowrap;
  }
  .contact-icons {
    position: absolute;
    left: 10px; width: 300px;
    top: 500px;
    display: flex;
    justify-content: center;
    align-items: center;
    gap: 8px;
  }
  .contact-icons .rule { width: 34px; height: 2px; background: var(--brand-red); }
  .contact-icons svg { width: 34px; height: 34px; }
  .contact-list {
    position: absolute;
    left: 10px; width: 300px;
    top: 544px;
    text-align: center;
    color: var(--ink-white);
    font-size: 21px;
    line-height: 32px;
    list-style: none;
    white-space: nowrap;
  }

  .brokerage-name {
    position: absolute;
    left: 40px; right: 40px;
    top: 500px;
    display: flex;
    align-items: center;
    justify-content: center;
    gap: 14px;
  }
  .brokerage-mark {
    width: 22px; height: 22px;
    background: var(--brand-red);
    flex: none;
  }
  .brokerage-text {
    color: var(--ink-white);
    font-weight: 800;
    font-size: 30px;
    line-height: 34px;
    text-transform: uppercase;
    letter-spacing: 0.5px;
  }
</style>
</head>
<body>
  <section class="card card-front">
    <svg class="front-shapes" viewBox="0 0 400 686" width="400" height="686">
      <defs>
        <linearGradient id="portraitTone" x1="0" y1="0" x2="0" y2="1">
          <stop offset="0" stop-color="#505052"/>
          <stop offset="1" stop-color="#444446"/>
        </linearGradient>
        <linearGradient id="figureTone" x1="0" y1="0" x2="0" y2="1">
          <stop offset="0" stop-color="#3a3a3e"/>
          <stop offset="1" stop-color="#26262a"/>
        </linearGradient>
        <clipPath id="aboveBand">
          <polygon points="0,0 400,0 400,500 0,200"/>
        </clipPath>
      </defs>
      <rect class="portrait-backdrop" x="0" y="0" width="400" height="520" fill="url(#portraitTone)"/>
      <rect class="portrait-area" x="110" y="70" width="270" height="450" rx="18" fill="url(#figureTone)" clip-path="url(#aboveBand)" role="img" aria-label="Portrait photo of Colin Vardek in a dark suit and white shirt"/>
      <polygon class="accent-band" points="0,200 400,500 400,512 0,255" fill="var(--brand-red)"/>
      <polygon class="info-panel" points="0,255 400,512 400,686 0,686" fill="var(--card-dark)"/>
    </svg>

    <h1 class="agent-name">Colin Vardek</h1>

    <div class="contact-icons">
      <span class="rule"></span>
      <svg viewBox="0 0 34 34" aria-label="Phone">
        <circle cx="17" cy="17" r="17" fill="var(--brand-red)"/>
        <path d="M12 10c1-1 2 0 3 2s0 2-1 3c1 2 3 4 5 5 1-1 1-2 3-1s3 2 2 3-2 2-4 2c-5-1-9-5-10-10 0-2 1-3 2-4z" fill="none" stroke="#fff" stroke-width="1.6"/>
      </svg>
      <svg viewBox="0 0 34 34" aria-label="Email">
        <circle cx="17" cy="17" r="17" fill="var(--brand-red)"/>
        <rect x="9" y="11.5" width="16" height="11" fill="#fff"/>
        <path d="M9 11.5l8 6.5 8-6.5" fill="none" stroke="var(--brand-red)" stroke-width="1.4"/>
      </svg>
      <svg viewBox="0 0 34 34" aria-label="Website">
        <circle cx="17" cy="17" r="17" fill="var(--brand-red)"/>
        <g fill="none" stroke="#fff" stroke-width="1.4">
          <circle cx="17" cy="17" r="8"/>
          <ellipse cx="17" cy="17" rx="3.5" ry="8"/>
          <line x1="9" y1="17" x2="25" y2="17"/>
          <line x1="10.5" y1="13" x2="23.5" y2="13"/>
          <line x1="10.5" y1="21" x2="23.5" y2="21"/>
        </g>
      </svg>
      <span class="rule"></span>
    </div>

    <ul class="contact-list">
      <li class="contact-phone">587-412-9065</li>
      <li class="contact-email">colinvardek@mailora.com</li>
      <li class="contact-web">colinvardek.ca</li>
    </ul>
  </section>

  <section class="card card-back">
    <div class="brokerage-name">
      <span class="brokerage-mark"></span>
      <span class="brokerage-text">The Harbourline<br>Property Group</span>
    </div>
  </section>
</body>
</html>
```